Low Ferry Guild - Wavering CD Cover

To prepare a CD Cover for the single "Wavering" by Low Ferry Guild.
You can hear the single here:
http://lowferryguild-band.example/listen/

The LFG logo and backdrop are also provided if you want to incorporate them into the CD cover design, though that isn't mandatory.

Song is about deciding on taking on a serious relationship, and leaving the single life behind.

Target Market(s)

Music listeners, 18-50 yrs old, into retro 80s, Marrowmen/Tide Rollers

Industry/Entity Type

Music Download

Requirements
Must have
• LFG logo
• Wavering title
Nice to have
• Use of backdrop, or facimile
Should not have
• Too obvious on the term Wavering

```html
<!DOCTYPE html>
<html lang="en">
<head>
<meta charset="utf-8">
<title>Low Ferry Guild – Wavering CD Cover</title>
<link rel="stylesheet" href="https://fonts.googleapis.com/css2?family=Big+Shoulders+Display:wght@400&display=swap">
<style>
  :root {
    --stage: #1f222b;
    --night: #0c1322;
    --ink-blue: #13294a;
    --deep-blue: #1b4b82;
    --glow-blue: #3a78bb;
    --haze: #8fb0d4;
    --ink: #ffffff;
  }
  html, body {
    margin: 0;
    padding: 0;
    width: 1200px;
    height: 1114px;
    overflow: hidden;
    background: var(--stage);
  }
  .cover {
    position: absolute;
    left: 134px;
    top: 94px;
    width: 936px;
    height: 902px;
    overflow: hidden;
    background: var(--night);
  }
  .cover svg {
    display: block;
    width: 936px;
    height: 902px;
  }
  .band-name {
    font-family: "Big Shoulders Display", "Arial Narrow", sans-serif;
    font-weight: 400;
    fill: var(--ink);
  }
  .title-lettering {
    fill: var(--ink);
    opacity: 0.9;
  }
</style>
</head>
<body>
  <main class="cover" aria-label="CD cover for the single Wavering by Low Ferry Guild">
    <svg viewBox="0 0 936 902" xmlns="http://www.w3.org/2000/svg">
      <defs>
        <radialGradient id="bokeh-glow" cx="0.62" cy="0.4" r="0.8" fx="0.66" fy="0.36">
          <stop offset="0" stop-color="var(--haze)"/>
          <stop offset="0.18" stop-color="var(--glow-blue)"/>
          <stop offset="0.45" stop-color="var(--deep-blue)"/>
          <stop offset="0.75" stop-color="var(--ink-blue)"/>
          <stop offset="1" stop-color="var(--night)"/>
        </radialGradient>
      </defs>

      <rect class="backdrop" width="936" height="902" fill="url(#bokeh-glow)"
            role="img" aria-label="Out-of-focus blue bokeh lights scattered over a dark night background"/>

      <g class="band-name" aria-label="Low Ferry Guild">
        <text x="328" y="328" font-size="187" textLength="288" lengthAdjust="spacingAndGlyphs">LOW</text>
        <text x="328" y="494" font-size="170" textLength="288" lengthAdjust="spacingAndGlyphs">FERRY</text>
        <text x="328" y="616" font-size="110" textLength="288" lengthAdjust="spacingAndGlyphs">GUILD</text>
      </g>

      <rect class="title-lettering" x="334" y="650" width="278" height="66" rx="33"
            role="img" aria-label="Hand-lettered white brush title: Wavering"/>
    </svg>
  </main>
</body>
</html>
```